Crestview Imaging Center Brochure

We need a color brochure to highlight to our customers, patients, and referring physicians what we do, why the patients should visit our business compared to our competition. I want to emphasis that we are most concerning with delivering excellent patient care in regards to safety, an excellent patient experience and delivering high quality, meaningful imaging reports by the best radiologists.

I would like to add additional pictures to the brochure that, but not certain what to include some generic patient pictures, sports players, or family pictures that will connect with our potential clients. Any ideas are welcome.

Target Market(s)

patient and referring docs

Industry/Entity Type

Medical Imaging

Colors
0355a3
ffffff

Requirements
Must have
• a consistent look and feel with our website www.crestviewimagingctr.com to have a unified "brand"
Nice to have
• clean professional look

```html
<!DOCTYPE html>
<html lang="en">
<head>
<meta charset="utf-8">
<title>Crestview Imaging Center Brochure</title>
<link rel="stylesheet" href="https://fonts.googleapis.com/css2?family=Source+Sans+3:wght@400;600&display=swap">
<style>
  :root {
    --brand-blue: #1873bd;
    --deep-blue: #0355a3;
    --sky-band: #b7d4eb;
    --heading-blue: #1570b9;
    --body-text: #3a3a3a;
    --white: #ffffff;
  }
  * { margin: 0; padding: 0; box-sizing: border-box; }
  html, body { width: 1200px; height: 927px; overflow: hidden; background: var(--white); }
  .brochure {
    position: relative;
    width: 1200px;
    height: 927px;
    overflow: hidden;
    font-family: "Source Sans 3", "Myriad Pro", Arial, sans-serif;
    color: var(--body-text);
    background: var(--white);
  }
  .hero-photo {
    position: absolute;
    left: 404px; top: 60px;
    width: 796px; height: 416px;
    background: linear-gradient(100deg, #d9dde2 0%, #f1ebe6 22%, #3a4a5e 48%, #2b2e33 70%, #555a60 100%);
  }
  .top-wave {
    position: absolute;
    left: 0; top: 0;
    width: 1200px; height: 200px;
  }
  .sign-photo {
    position: absolute;
    left: 0; top: 582px;
    width: 398px; height: 345px;
    background: linear-gradient(180deg, #e8eef2 0%, #b9c4b0 35%, #8b5360 52%, #2a2a2e 70%, #c9c2b4 88%, #6f8f4a 100%);
  }
  .bottom-band {
    position: absolute;
    left: 398px; top: 850px;
    width: 802px; height: 77px;
    background: var(--brand-blue);
    border-top: 12px solid var(--sky-band);
  }
  .web-address {
    position: absolute;
    right: 16px; bottom: 16px;
    font-size: 15.5px;
    color: var(--white);
    letter-spacing: 0.1px;
  }
  .section-title {
    position: absolute;
    font-weight: 400;
    font-size: 34px;
    line-height: 1;
    color: var(--heading-blue);
    white-space: nowrap;
  }
  .section-body {
    position: absolute;
    font-size: 12.6px;
    line-height: 16.3px;
    text-align: justify;
  }
  .section-body strong { font-weight: 600; }
  .about .section-title { left: 50px; top: 124px; }
  .about .section-body { left: 50px; top: 174px; width: 300px; }
  .why .section-title { left: 453px; top: 520px; }
  .why .section-body { left: 453px; top: 571px; width: 297px; }
  .expertise .section-title { left: 840px; top: 520px; }
  .expertise .section-body { left: 851px; top: 571px; width: 301px; }
</style>
</head>
<body>
<div class="brochure">
  <div class="hero-photo" role="img" aria-label="Smiling radiologist in a white coat seated in front of several monitors displaying MRI scans"></div>

  <svg class="top-wave" viewBox="0 0 1200 200" aria-hidden="true">
    <path d="M0 0 H1200 V176 C1020 95 700 58 420 62 C250 65 100 90 0 130 Z" fill="var(--sky-band)"/>
    <path d="M0 0 H1200 V166 C1020 86 700 48 420 52 C250 55 100 80 0 118 Z" fill="var(--brand-blue)"/>
    <path d="M0 130 C100 90 250 65 420 62 L420 64 L0 140 Z" fill="var(--white)" opacity="0"/>
  </svg>

  <section class="about">
    <h2 class="section-title">About Crestview Imaging</h2>
    <p class="section-body">Crestview Imaging Center, a division of Harlow and Associates, P.C., was established in 2015. We identified a need in our communities to provide a better product for our patients when choosing MRI providers. As a physician owned practice, we pride ourselves on providing High Quality, Accurate Reports, Rapid Results (a final report within 24 hours), availability for consultations/discussion with the radiologists, and Convenient care for our patients without having to get lost in the maze of a hospital. Harlow and Associates, PC is a full service imaging and interventional radiology group composed of 10 Michigan based, board certified radiologists with subspecialty training in Neuroradiology, Musculoskeletal Radiology, Body Imaging, Women's Imaging, Nuclear Radiology, and Interventional Radiology. Our group through partnering with physicians and health care institutions is committed to provide quality, timely, and efficient services with the ultimate goal of providing better health care to our patients and their physicians. Since our inception in 1979, we have had a strong history of providing high quality imaging services to Southeastern and Central Michigan. We look forward to being a complete solution for your imaging needs.</p>
  </section>

  <div class="sign-photo" role="img" aria-label="Outdoor monument sign in front of the imaging center building with landscaped grasses"></div>

  <section class="why">
    <h2 class="section-title">Why Crestview Imaging?</h2>
    <p class="section-body">Crestview Imaging Center puts patient care at the center of all we do. Whether your dealing with a knee injury or a complex cancer diagnosis, compassionate care is part of Crestview Imaging Center. Crestview Imaging Center utilizes Veltrix equipment, with its unique short bore design and advanced acquisition technology, this allows for improved patient comfort, openness, and reduced scan times. You can be confident that our radiologists will deliver consistent, accurate, timely, and dependable reports that you and your doctor can rely on to have a meaningful impact in your care plan and treatment decisions. From diagnosis, to treatment, and recovery, our team works with your physician to quickly and accurately address your medical needs.</p>
  </section>

  <section class="expertise">
    <h2 class="section-title">Our areas of Expertise</h2>
    <p class="section-body">With our diverse subspecialty trained radiologists, Crestview Imaging Center will provide expertise in imaging all areas of the body. We have neuroradiologists that are trained to evaluate diseases of the brain and spine, musculoskeletal radiologist that are the experts in imaging of sports injuries and bone/muscle tumors, as well as body imaging radiologists which specialize in the imaging evaluation of abdominal and pelvis diseases. We perform MRI exams both with and without intravenous contrast and we are able to perform MRI arthrogram exams or all joints.<br><strong>Insurances accepted:</strong><br>For your convenience we participate with nearly all insurance carriers. We also have Self-pay options for those patients with high deductibles or no insurance.</p>
  </section>

  <footer class="bottom-band">
    <span class="web-address">www.crestviewimagingctr.com</span>
  </footer>
</div>
</body>
</html>
```